3D Printing Website redesign

We are in the process of redesigning our website. Attached is an image of one of the proposed pages - "The Quillmarrow". The idea with this page is that site visitors can get an indicative estimate of the cost of 3D Printing based on some provided metrics. When the user alters the metrics the price changes accordingly. We are looking for a design to support this page that will also be used across our site.

Reason: Allow more time for designers to submit designs

Reason: Still looking for the design to blow us away!

Printing

```html
<!DOCTYPE html>
<html lang="en">
<head>
<meta charset="utf-8">
<title>Layerfield Studio</title>
<link rel="stylesheet" href="https://fonts.googleapis.com/css2?family=Source+Sans+3:wght@400;600;700&family=Yanone+Kaffeesatz:wght@400&display=swap">
<style>
  :root {
    --paper: #f4f4f4;
    --ink-grey: #7a7a7a;
    --nav-blue: #1f4987;
    --nav-blue-dark: #183c72;
    --nav-line: #2f5b9c;
    --active-cyan: #00aeef;
    --brand-blue: #1a63b3;
    --badge-grey: #b9bdc5;
    --page-blue: #2a4778;
    --page-blue-dark: #233d69;
    --slide-grey: #787878;
    --caption-blue: #2f5189;
    --arrow-navy: #12162f;
    --search-fill: #e4e6f1;
    --white: #ffffff;
    --body-text: #cfd6e5;
    --quote-text: #8e9fc0;
  }
  * { margin: 0; padding: 0; box-sizing: border-box; }
  html, body { width: 1200px; height: 895px; overflow: hidden; }
  body {
    position: relative;
    font-family: "Source Sans 3", "Myriad Pro", sans-serif;
    background: var(--paper);
  }
  .site-header {
    position: absolute; left: 0; top: 0; width: 1200px; height: 315px;
    background: var(--paper);
  }
  .contact-block {
    position: absolute; left: 126px; top: 11px;
    color: var(--ink-grey); font-size: 15.5px; line-height: 17.3px;
  }
  .account-button {
    position: absolute; left: 1047px; top: 0; width: 50px; height: 47px;
    background: var(--nav-blue);
    display: flex; align-items: center; justify-content: center;
  }
  .search-box {
    position: absolute; left: 872px; top: 58px; width: 225px; height: 47px;
    background: var(--search-fill); border: 1px solid var(--nav-blue);
    display: flex; align-items: center; justify-content: space-between;
    padding: 0 16px 0 18px; color: #2a2f45; font-size: 16px;
  }
  .main-nav {
    position: absolute; left: 0; top: 112px; width: 1200px; height: 56px;
    background: linear-gradient(var(--nav-blue), var(--nav-blue-dark));
    box-shadow: 0 2px 3px rgba(0,0,0,.25);
  }
  .nav-item {
    position: absolute; top: 0; height: 56px;
    display: flex; align-items: center; justify-content: center;
    color: var(--white); font-size: 16px; font-weight: 600;
    border-left: 1px solid var(--nav-line);
  }
  .nav-item.is-active { background: var(--active-cyan); border-color: var(--active-cyan); }
  .nav-end { border-right: 1px solid var(--nav-line); }
  .brand-badge {
    position: absolute; left: 490px; top: 8px; width: 200px; height: 196px;
    border-radius: 50%; background: var(--badge-grey);
  }
  .brand-name {
    position: absolute; left: 0; top: 196px; width: 1200px; text-align: center;
    color: var(--brand-blue); font-size: 70px; font-weight: 700; letter-spacing: 6px;
    line-height: 80px;
  }
  .page-body {
    position: absolute; left: 0; top: 315px; width: 1200px; height: 580px;
    background: linear-gradient(var(--page-blue), var(--page-blue-dark));
  }
  .slide-image {
    position: absolute; left: 182px; top: 38px; width: 835px; height: 408px;
    background: var(--slide-grey);
  }
  .slide-caption {
    position: absolute; font-family: "Yanone Kaffeesatz", "Arial Narrow", sans-serif;
    color: var(--white); font-size: 50px; line-height: 52px; background: var(--caption-blue);
  }
  .caption-top { left: 713px; top: 339px; width: 304px; height: 52px; padding-left: 15px; }
  .caption-bottom { left: 679px; top: 387px; width: 338px; height: 58px; padding-left: 22px; }
  .slide-arrow {
    position: absolute; top: 392px; width: 54px; height: 54px; background: var(--arrow-navy);
    display: flex; align-items: center; justify-content: center;
  }
  .arrow-prev { left: 182px; }
  .arrow-next { left: 237px; }
  .welcome-title {
    position: absolute; left: 130px; top: 490px;
    color: var(--white); font-size: 49px; font-weight: 400; line-height: 60px;
  }
  .welcome-text {
    position: absolute; left: 130px; top: 548px; width: 500px;
    color: var(--body-text); font-size: 12.5px; line-height: 18px;
  }
  .intro-quote {
    position: absolute; left: 739px; top: 503px; width: 360px;
    color: var(--quote-text); font-size: 22px; line-height: 26px;
  }
</style>
</head>
<body>
  <header class="site-header">
    <address class="contact-block" style="font-style:normal">
      Layerfield Studio<br>
      Shop 7, 12 - 16 Harbour Lane, Millers Point, Sydney 2000<br>
      Ph: 61 2 5550 1234<br>
      M: 0400 555 219<br>
      e-mail: hello@layerfieldstudio.com.au
    </address>

    <a class="account-button" aria-label="Account">
      <svg width="22" height="22" viewBox="0 0 22 22"><circle cx="11" cy="7" r="5" fill="#fff"/><path d="M1 21c0-6 4-8 10-8s10 2 10 8z" fill="#fff"/></svg>
    </a>

    <div class="search-box">
      <span>Search...</span>
      <svg width="18" height="18" viewBox="0 0 18 18"><circle cx="7.5" cy="7.5" r="5.5" fill="none" stroke="#2a2f45" stroke-width="2"/><path d="M11.5 11.5l5 5" stroke="#2a2f45" stroke-width="2.4" stroke-linecap="round"/></svg>
    </div>

    <div class="brand-name">LAYERFIELD STUDIO</div>

    <nav class="main-nav">
      <a class="nav-item" style="left:102px;width:76px">HOME</a>
      <a class="nav-item" style="left:178px;width:80px">SHOP</a>
      <a class="nav-item is-active" style="left:258px;width:87px">PRICES</a>
      <a class="nav-item" style="left:345px;width:110px">MATERIALS</a>
      <a class="nav-item" style="left:695px;width:103px">GALLERY</a>
      <a class="nav-item" style="left:798px;width:107px">TRAINING</a>
      <a class="nav-item" style="left:905px;width:112px">ABOUT US</a>
      <a class="nav-item nav-end" style="left:1017px;width:80px">BLOG</a>
    </nav>

    <div class="brand-badge" aria-hidden="true"></div>
  </header>

  <main class="page-body">
    <div class="slide-image" role="img" aria-label="Featured slide image"></div>
    <div class="slide-caption caption-top">BEST STORY YOU</div>
    <div class="slide-caption caption-bottom">HAVE EVER HEARD</div>
    <a class="slide-arrow arrow-prev" aria-label="Previous slide">
      <svg width="14" height="18" viewBox="0 0 14 18"><path d="M10 2L3 9l7 7" fill="none" stroke="#fff" stroke-width="3"/></svg>
    </a>
    <a class="slide-arrow arrow-next" aria-label="Next slide">
      <svg width="14" height="18" viewBox="0 0 14 18"><path d="M4 2l7 7-7 7" fill="none" stroke="#fff" stroke-width="3"/></svg>
    </a>

    <h1 class="welcome-title">Welcome to our company</h1>
    <p class="welcome-text">Sed gravida ligula vel arcu luctus sed tristique quam pharetra. Phasellus nisl libero, varius nec trist interdum ac, commodo et felis. Praesent porttitor facilisis dictum. Vivamus nulla mi, ultricies et dictu</p>

    <blockquote class="intro-quote">“Sed gravida ligula vel arcu luctus sed tristique quam pharetra porttitor vel facilisis dictum vel arcu igula quam.”</blockquote>
  </main>
</body>
</html>
```